Business Card Design for sports performance / psychology company

You can see my website that this is based upon here:
http://www.trelvanedge.co.uk

More than happy to answer any additional questions that you might have

** Happy for any images from Pixelvault to be used. If I go with your design I will purchase the image for you to use

Target Market(s)

Football players

Industry/Entity Type

Business

Contact Information for Business Card

Name: Clive Arnott
Title: Clinical Hypnotherapist & Strategist
Email address: clive@trelvanedge.co.uk
Tel: 07912486015

Font styles to use
Other font styles liked:
• Same font as on website. I'm not actually sure what it is

Requirements
Must have
• Tagline:
• Skill x Focus = Results
• Don't put form down to chance
Nice to have
• Happy for designers to be creative
Should not have

```html
<!DOCTYPE html>
<html lang="en">
<head>
<meta charset="utf-8">
<title>Trelvan Edge – Business Card</title>
<link rel="stylesheet" href="https://fonts.googleapis.com/css2?family=Jost:wght@400&family=Lato:wght@300;400;700&display=swap">
<style>
  :root {
    --backdrop: #232323;
    --card: #ffffff;
    --navy: #231d4a;
    --ink: #3a3a3a;
    --rule: #231d4a;
  }
  * { box-sizing: border-box; margin: 0; padding: 0; }
  html, body { width: 1189px; height: 1200px; overflow: hidden; }
  body { background: var(--backdrop); position: relative; font-family: "Lato", sans-serif; }

  .card {
    position: absolute;
    left: 171px;
    width: 856px;
    height: 488px;
    background: var(--card);
    border-radius: 34px;
  }
  .card--front { top: 67px; }
  .card--back  { top: 627px; }

  /* Front */
  .front-mark {
    position: absolute; left: 50%; top: 142px;
    width: 70px; height: 70px; margin-left: -35px;
    background: var(--navy);
  }
  .brand-name {
    position: absolute; left: 0; right: 0; top: 250px;
    text-align: center;
    font-family: "Jost", sans-serif; font-weight: 400;
    font-size: 70px; letter-spacing: 3px; line-height: 1;
    color: var(--navy);
  }
  .tagline {
    position: absolute; left: 0; right: 0; top: 322px;
    text-align: center;
    font-family: "Lato", sans-serif; font-weight: 400;
    font-size: 24px; color: var(--ink);
  }

  /* Back */
  .back-brand {
    position: absolute; left: 74px; top: 105px; width: 253px; height: 280px;
    display: flex; flex-direction: column; align-items: center; justify-content: center; gap: 22px;
  }
  .back-brand__square { width: 150px; height: 150px; background: var(--navy); }
  .back-brand__name {
    font-family: "Jost", sans-serif; font-weight: 400;
    font-size: 30px; letter-spacing: 1px; color: var(--navy);
  }
  .divider {
    position: absolute; left: 376px; top: 105px; width: 2px; height: 280px;
    background: var(--rule);
  }
  .details { position: absolute; left: 425px; top: 100px; color: var(--ink); }
  .person-name { font-size: 32px; color: var(--navy); font-weight: 300; line-height: 1.1; }
  .person-name strong { font-weight: 700; }
  .person-title { font-size: 23px; font-weight: 300; margin-top: 2px; }
  .address { margin-top: 60px; font-size: 24px; font-weight: 300; line-height: 28px; }
  .contacts { list-style: none; margin-top: 22px; font-size: 24px; font-weight: 300; }
  .contacts li { display: flex; align-items: center; gap: 12px; height: 28px; }
  .contacts svg { width: 22px; height: 22px; flex: none; }
  .contacts .accent { color: var(--navy); font-weight: 400; }
</style>
</head>
<body>
  <section class="card card--front">
    <div class="front-mark"></div>
    <h1 class="brand-name">TRELVAN EDGE</h1>
    <p class="tagline">Skill x Focus = Results</p>
  </section>

  <section class="card card--back">
    <div class="back-brand">
      <div class="back-brand__square"></div>
      <span class="back-brand__name">TRELVAN EDGE</span>
    </div>
    <div class="divider"></div>
    <div class="details">
      <p class="person-name"><strong>Clive</strong> Arnott</p>
      <p class="person-title">Clinical Hypnotherapist &amp; Strategist</p>
      <p class="address">Tamarind Research Park<br>Kestrow &amp; Marlowe Street, Ashby</p>
      <ul class="contacts">
        <li>
          <svg viewBox="0 0 22 22" aria-hidden="true"><rect width="22" height="22" rx="3" fill="#231d4a"/><path d="M5 9c0-2 3-3 6-3s6 1 6 3l-2 1-1-2H8L7 10z M7 11h8l1 5H6z" fill="#fff"/></svg>
          <span>07912486015</span>
        </li>
        <li>
          <svg viewBox="0 0 22 22" aria-hidden="true"><rect width="22" height="22" rx="3" fill="#231d4a"/><rect x="4.5" y="6.5" width="13" height="9" fill="none" stroke="#fff" stroke-width="1.4"/><path d="M4.5 6.5l6.5 5 6.5-5M4.5 15.5l5-4.5M17.5 15.5l-5-4.5" fill="none" stroke="#fff" stroke-width="1.2"/></svg>
          <span>clive@trelvanedge.co.uk</span>
        </li>
        <li>
          <svg viewBox="0 0 22 22" aria-hidden="true"><rect width="22" height="22" rx="3" fill="#231d4a"/><circle cx="11" cy="11" r="6.5" fill="none" stroke="#fff" stroke-width="1.2"/><ellipse cx="11" cy="11" rx="3" ry="6.5" fill="none" stroke="#fff" stroke-width="1"/><path d="M4.5 11h13M5.5 8h11M5.5 14h11" stroke="#fff" stroke-width="1"/></svg>
          <span>www.<span class="accent">trelvanedge</span>.co.uk</span>
        </li>
      </ul>
    </div>
  </section>
</body>
</html>
```